Pellham Grove Trust - New Website Designed

I need a site that looks like this http://www.quorlandgiving.org for boat donations. So please replace the cars with boats.

```html
<!DOCTYPE html>
<html lang="en">
<head>
<meta charset="utf-8">
<title>Pellham Grove Trust – Boat Donation</title>
<link href="https://fonts.googleapis.com/css2?family=Lato:wght@400;700;900&family=Open+Sans:wght@400;600&display=swap" rel="stylesheet">
<style>
:root{
  --navy:#0b2a6f;
  --navy-deep:#1c3f85;
  --red:#c8102e;
  --ink:#141414;
  --muted:#6a6a6a;
  --pale:#eef2f8;
  --line:#d9d9d9;
  --white:#ffffff;
  --panel:rgba(40,46,56,.82);
}
*{box-sizing:border-box;margin:0;padding:0}
html,body{width:1200px;height:2546px;overflow:hidden;background:var(--white)}
body{position:relative;font-family:"Open Sans",Arial,sans-serif;color:var(--ink)}
.abs{position:absolute}
.heading{font-family:"Lato",Arial,sans-serif;font-weight:900;text-transform:uppercase}

/* header */
.site-name{left:98px;top:32px;font-family:"Lato",sans-serif;font-weight:900;font-size:25px;color:var(--ink);letter-spacing:.2px}
.callout{left:832px;top:8px;display:flex;align-items:flex-start;gap:10px}
.callout .ring{width:32px;height:32px;border:2px solid var(--red);border-radius:50%;display:flex;align-items:center;justify-content:center;margin-top:2px}
.callout .call{font-family:"Lato",sans-serif;font-size:17px;color:var(--ink)}
.callout .call b{font-size:22px;font-weight:900;color:var(--navy)}
.callout .hours{font-family:"Lato",sans-serif;font-weight:700;font-size:12.5px;margin-top:1px}
.main-nav{left:421px;top:66px;display:flex;gap:0;font-family:"Lato",sans-serif;font-weight:700;font-size:15px}
.main-nav span{position:absolute;white-space:nowrap}
.main-nav .active{color:var(--red)}

/* hero */
.hero-photo{left:0;top:97px;width:1200px;height:477px;background:linear-gradient(180deg,#5b6e82 0%,#3e556b 45%,#1e3a55 70%,#2c4a66 100%)}
.donate-panel{left:709px;top:97px;width:391px;height:477px;background:var(--panel)}
.donate-title{left:0;top:0;width:391px;height:49px;background:var(--navy);color:var(--white);font-size:22px;text-align:center;line-height:49px}
.donate-intro{left:19px;top:64px;color:var(--white);font-size:13.5px;white-space:nowrap}
.donate-intro b{font-family:"Lato",sans-serif;font-size:17px;font-weight:900}
.field label{display:block;color:var(--white);font-size:12.5px;margin-bottom:6px}
.field .box{width:175px;height:29px;border:1px solid #cfd3d9;background:rgba(20,24,30,.25);position:relative}
.field .arrow{position:absolute;right:0;top:0;width:29px;height:27px;border-left:1px solid #cfd3d9;display:flex;align-items:center;justify-content:center}
.donate-btn{left:19px;top:407px;width:355px;height:44px;border-radius:22px;background:var(--red);color:var(--white);font-size:15px;text-align:center;line-height:44px}

/* program band */
.program{left:0;top:574px;width:1200px;height:130px;background:var(--white);border-bottom:2px solid var(--line)}
.program-flag{left:0;top:0}
.program-title{left:98px;top:34px;color:var(--white);font-size:25px;line-height:33px}
.perk{width:200px;text-align:center;font-family:"Lato",sans-serif;font-weight:700;font-size:16px;line-height:20px;color:var(--ink)}
.perk svg{display:block;margin:0 auto 10px}

/* welcome */
.welcome-title{left:98px;top:799px;font-size:24px;letter-spacing:-.2px;white-space:nowrap}
.welcome-copy{left:98px;top:855px;width:460px;font-size:12.6px;line-height:22px;color:#555}
.welcome-copy p+p{margin-top:18px}
.outline-btn{border:1px solid #9a9a9a;border-radius:20px;color:var(--red);font-family:"Lato",sans-serif;font-weight:900;font-size:13px;text-align:center}
.video-frame{left:599px;top:789px;width:501px;height:328px;border:1px solid #cfcfcf;padding:4px;background:var(--white)}
.video-fill{width:100%;height:100%;background:linear-gradient(135deg,#c9a27a 0%,#8b6b52 40%,#9aa7a0 70%,#5f6b52 100%);position:relative}
.play{position:absolute;left:50%;top:50%;width:56px;height:56px;margin:-28px 0 0 -28px;border-radius:50%;background:rgba(0,0,0,.75)}

/* why */
.why{left:0;top:1196px;width:1200px;height:464px;background:var(--pale)}
.section-title{width:1200px;text-align:center;font-size:27px}
.reason{width:240px;text-align:center}
.reason .badge{width:152px;height:152px;border-radius:50%;border:3px solid var(--navy);margin:0 auto;display:flex;align-items:center;justify-content:center}
.reason .badge .inner{width:128px;height:128px;border-radius:50%;border:1px solid #aab3c6;display:flex;align-items:center;justify-content:center}
.reason h3{font-family:"Lato",sans-serif;font-weight:700;font-size:19px;margin-top:38px;white-space:nowrap}
.reason p{font-size:11.5px;line-height:24px;color:var(--muted);margin-top:6px}

/* how */
.how{left:0;top:1660px;width:1200px;height:512px;background:linear-gradient(180deg,#1e4288 0%,#1a3c80 55%,#21468a 100%)}
.step{width:380px;text-align:center;color:var(--white)}
.step .disc{width:170px;height:170px;border-radius:50%;border:1.5px solid rgba(255,255,255,.75);margin:0 auto;display:flex;align-items:center;justify-content:center;position:relative}
.step .num{position:absolute;left:50%;bottom:-16px;width:30px;height:30px;margin-left:-15px;background:var(--white);transform:rotate(45deg)}
.step .num span{display:block;transform:rotate(-45deg);color:var(--red);font-family:"Lato",sans-serif;font-weight:900;font-size:17px;line-height:30px}
.step h3{font-family:"Lato",sans-serif;font-weight:700;font-size:20px;margin-top:42px}
.step p{font-size:12.5px;line-height:26px;margin-top:6px}

/* footer */
.footer-name{left:98px;top:2340px;font-family:"Lato",sans-serif;font-weight:900;font-size:25px;white-space:nowrap}
.col-title{font-family:"Lato",sans-serif;font-weight:900;font-size:16px;text-transform:uppercase;white-space:nowrap}
.quick-links{left:423px;top:2267px}
.quick-links ul{list-style:none;margin-top:22px;font-size:12px;color:#555;line-height:24px}
.newsletter{left:585px;top:2267px;width:260px}
.newsletter p{font-size:12px;color:#555;line-height:20px;margin-top:20px}
.newsletter .email{margin-top:12px;border-bottom:1px solid #bdbdbd;padding:6px 0;font-size:11.5px;color:#9a9a9a;width:255px}
.contact{left:894px;top:2267px}
.contact .row{display:flex;gap:16px;font-size:12px;color:#555;line-height:20px;margin-top:18px}
.contact .row svg{flex:none;margin-top:3px}
.rule{left:98px;top:2466px;width:1004px;height:1px;background:var(--line)}
.copyright{left:98px;top:2495px;font-size:11.5px;color:#555}
.socials{left:980px;top:2488px;display:flex;gap:8px}
.socials span{width:26px;height:26px;border-radius:50%;border:1px solid #8a8a8a;display:block}
</style>
</head>
<body>

<header>
  <div class="abs site-name">PELLHAM GROVE TRUST</div>
  <div class="abs callout">
    <div class="ring"><svg width="16" height="16" viewBox="0 0 24 24"><path fill="#c8102e" d="M6.6 10.8a15 15 0 006.6 6.6l2.2-2.2c.3-.3.7-.4 1-.2 1.1.4 2.3.6 3.6.6.6 0 1 .4 1 1V20c0 .6-.4 1-1 1A17 17 0 013 4c0-.6.4-1 1-1h3.5c.6 0 1 .4 1 1 0 1.3.2 2.5.6 3.6.1.3 0 .7-.2 1z"/></svg></div>
    <div>
      <div class="call">Call <b>1-800-555-0142</b></div>
      <div class="hours">Live operator available 7 days a week</div>
    </div>
  </div>
  <nav class="abs main-nav">
    <span class="active" style="left:0">HOME</span>
    <span style="left:79px">ABOUT</span>
    <span style="left:166px">HOW TO DONATE</span>
    <span style="left:327px">WHY DONATE</span>
    <span style="left:463px">NEWS</span>
    <span style="left:539px">CONTACT US</span>
    <span style="left:674px;top:2px"><svg width="15" height="15" viewBox="0 0 24 24"><circle cx="10" cy="10" r="7" fill="none" stroke="#141414" stroke-width="3"/><path d="M15 15l7 7" stroke="#141414" stroke-width="3"/></svg></span>
  </nav>
</header>

<section>
  <div class="abs hero-photo" role="img" aria-label="A service member holding a baby in front of a motor boat on open water"></div>
  <form class="abs donate-panel">
    <div class="abs donate-title heading">Donate Your Boat</div>
    <div class="abs donate-intro">Please fill out form or Call toll-free <b>1-800-555-0199</b></div>

    <div class="abs field" style="left:19px;top:110px"><label>Name:</label><div class="box"></div></div>
    <div class="abs field" style="left:199px;top:110px"><label>Email:</label><div class="box"></div></div>
    <div class="abs field" style="left:19px;top:169px"><label>Phone:</label><div class="box"></div></div>
    <div class="abs field" style="left:199px;top:169px"><label>Cell Phone:</label><div class="box"></div></div>
    <div class="abs field" style="left:19px;top:229px"><label>Address:</label><div class="box"></div></div>
    <div class="abs field" style="left:199px;top:229px"><label>City:</label><div class="box"></div></div>
    <div class="abs field" style="left:19px;top:287px"><label>Choose Year:</label><div class="box"><div class="arrow"><svg width="10" height="6" viewBox="0 0 10 6"><path d="M0 0h10L5 6z" fill="#fff"/></svg></div></div></div>
    <div class="abs field" style="left:199px;top:287px"><label>Choose Model:</label><div class="box"><div class="arrow"><svg width="10" height="6" viewBox="0 0 10 6"><path d="M0 0h10L5 6z" fill="#fff"/></svg></div></div></div>
    <div class="abs field" style="left:19px;top:346px"><label>State:</label><div class="box"><div class="arrow"><svg width="10" height="6" viewBox="0 0 10 6"><path d="M0 0h10L5 6z" fill="#fff"/></svg></div></div></div>
    <div class="abs field" style="left:199px;top:346px"><label>Zip Code:</label><div class="box"></div></div>

    <div class="abs donate-btn heading">Click Here to Donate Now!</div>
  </form>
</section>

<section class="abs program">
  <svg class="abs program-flag" width="350" height="130" viewBox="0 0 350 130"><path d="M0 0H288L350 65L288 130H0Z" fill="#0b2a6f"/></svg>
  <div class="abs program-title heading">Boat Donation<br>Program</div>

  <div class="abs perk" style="left:380px;top:20px">
    <svg width="40" height="40" viewBox="0 0 40 40"><circle cx="20" cy="20" r="18" fill="#c8102e"/><path d="M9 14c4 0 5 3 8 3s2 4 0 6-1 6-1 8M24 5c0 4 3 4 5 6s-1 5 2 7 4 1 6 1M22 28c2-2 5-1 6 2" fill="none" stroke="#fff" stroke-width="2"/></svg>
    Donation Accepted<br>Nation wide
  </div>
  <div class="abs perk" style="left:587px;top:20px">
    <svg width="48" height="40" viewBox="0 0 48 40"><rect x="2" y="8" width="44" height="26" fill="#c8102e"/><rect x="6" y="12" width="36" height="18" fill="none" stroke="#fff" stroke-width="1.5"/><circle cx="24" cy="21" r="7" fill="#fff"/><text x="24" y="25" font-family="Lato,sans-serif" font-weight="900" font-size="11" fill="#c8102e" text-anchor="middle">$</text></svg>
    You have<br>no costs
  </div>
  <div class="abs perk" style="left:766px;top:20px">
    <svg width="34" height="44" viewBox="0 0 34 44"><path d="M2 2h20l10 10v30H2z" fill="#c8102e"/><path d="M22 2v10h10" fill="#e9677b"/><path d="M8 20h18M8 26h18M8 32h18" stroke="#fff" stroke-width="2.5"/></svg>
    Tax<br>Deductible
  </div>
  <div class="abs perk" style="left:952px;top:20px">
    <svg width="40" height="40" viewBox="0 0 40 40"><circle cx="20" cy="20" r="18" fill="#c8102e"/><path d="M11 20l6 6 12-12" fill="none" stroke="#fff" stroke-width="4"/></svg>
    Towing is<br>Free
  </div>
</section>

<section>
  <h1 class="abs welcome-title heading">Welcome to Pellham Grove Trust</h1>
  <div class="abs welcome-copy">
    <p>Nemo enim ipsam voluptatem quia voluptas sit aspernatur aut odit aufugit, sed quia consequuntur magni dolores eo.</p>
    <p>Qui ratione voluptatem sequi nesciunt. Neque porro quisquam est, qui dolorem ipsum quia dolor sit amet, consectetur, adipisci velit, sed quia non num quam eius modi tempora incidunt ut labore et dolore magnam aliquam qua erat voluptanim ad minima veniam, quis no.</p>
  </div>
  <div class="abs outline-btn" style="left:98px;top:1067px;width:123px;height:38px;line-height:36px">READ MORE</div>
  <div class="abs video-frame">
    <div class="video-fill" role="img" aria-label="A military family standing together in front of their home with a flag">
      <div class="play"><svg width="56" height="56" viewBox="0 0 56 56"><path d="M22 17l17 11-17 11z" fill="#fff"/></svg></div>
    </div>
  </div>
</section>

<section class="abs why">
  <h2 class="abs section-title heading" style="left:0;top:62px">Why Donate Your Boat to Us?</h2>

  <div class="abs reason" style="left:79px;top:137px">
    <div class="badge"><div class="inner"><svg width="50" height="50" viewBox="0 0 40 40"><circle cx="20" cy="20" r="18" fill="#c8102e"/><path d="M11 20l6 6 12-12" fill="none" stroke="#fff" stroke-width="4"/></svg></div></div>
    <h3>Free Local Towing</h3>
    <p>Ut enim ad minima veniam, quis nos<br>trum exercitationem ullam</p>
  </div>
  <div class="abs reason" style="left:347px;top:137px">
    <div class="badge"><div class="inner"><svg width="44" height="54" viewBox="0 0 44 54"><rect x="2" y="2" width="40" height="50" rx="4" fill="#c8102e"/><rect x="8" y="8" width="28" height="10" fill="#fff"/><g fill="#fff"><rect x="8" y="23" width="7" height="6"/><rect x="18.5" y="23" width="7" height="6"/><rect x="29" y="23" width="7" height="6"/><rect x="8" y="32" width="7" height="6"/><rect x="18.5" y="32" width="7" height="6"/><rect x="29" y="32" width="7" height="6"/><rect x="8" y="41" width="7" height="6"/><rect x="18.5" y="41" width="7" height="6"/><rect x="29" y="41" width="7" height="6"/></g></svg></div></div>
    <h3>Tax Deduction</h3>
    <p>Ut enim ad minima veniam, quis nos<br>trum exercitationem ullam</p>
  </div>
  <div class="abs reason" style="left:613px;top:137px">
    <div class="badge"><div class="inner"><svg width="56" height="50" viewBox="0 0 56 50"><path d="M28 2L54 48H2Z" fill="#c8102e" stroke="#c8102e" stroke-width="3" stroke-linejoin="round"/><rect x="25.5" y="17" width="5" height="17" fill="#fff"/><rect x="25.5" y="38" width="5" height="5" fill="#fff"/></svg></div></div>
    <h3>No Paperwork Hassles</h3>
    <p>Ut enim ad minima veniam, quis nos<br>trum exercitationem ullam</p>
  </div>
  <div class="abs reason" style="left:880px;top:137px">
    <div class="badge"><div class="inner"><svg width="50" height="50" viewBox="0 0 50 50"><rect x="3" y="7" width="44" height="40" rx="3" fill="#c8102e"/><rect x="12" y="2" width="5" height="10" fill="#c8102e"/><rect x="33" y="2" width="5" height="10" fill="#c8102e"/><g fill="#fff"><rect x="9" y="18" width="7" height="6"/><rect x="18" y="18" width="7" height="6"/><rect x="27" y="18" width="7" height="6"/><rect x="36" y="18" width="6" height="6"/><rect x="9" y="27" width="7" height="6"/><rect x="18" y="27" width="7" height="6"/><rect x="27" y="27" width="7" height="6"/><rect x="36" y="27" width="6" height="6"/><rect x="9" y="36" width="7" height="6"/><rect x="18" y="36" width="7" height="6"/><rect x="27" y="36" width="7" height="6"/></g></svg></div></div>
    <h3>Schedule a Free Pickup</h3>
    <p>Ut enim ad minima veniam, quis nos<br>trum exercitationem ullam</p>
  </div>
</section>

<section class="abs how" role="img" aria-label="A motor yacht moored on calm water under a blue tint">
  <h2 class="abs section-title heading" style="left:0;top:68px;color:#fff">How It Works?</h2>

  <div class="abs step" style="left:34px;top:142px">
    <div class="disc"><svg width="60" height="60" viewBox="0 0 60 60"><path d="M36 10H10v40h40V26" fill="none" stroke="#fff" stroke-width="4"/><path d="M46 6l8 8-22 22-10 2 2-10z" fill="#fff"/></svg><div class="num"><span>1</span></div></div>
    <h3>Fill out the simple form</h3>
    <p>Neque porro quisquam est, qui dolorem<br>ipsum quia dolor sit am consect</p>
  </div>
  <div class="abs step" style="left:409px;top:142px">
    <div class="disc"><svg width="50" height="62" viewBox="0 0 34 44"><path d="M2 2h20l10 10v30H2z" fill="#fff"/><path d="M22 2v10h10" fill="#bcc8e0"/><path d="M8 20h18M8 26h18M8 32h18" stroke="#1c3f85" stroke-width="2.5"/></svg><div class="num"><span>2</span></div></div>
    <h3>Schedule your free pick-up</h3>
    <p>Neque porro quisquam est, qui dolorem<br>ipsum quia dolor sit am consect</p>
  </div>
  <div class="abs step" style="left:781px;top:142px">
    <div class="disc"><svg width="46" height="62" viewBox="0 0 46 62"><rect x="4" y="2" width="38" height="58" fill="#fff"/><g fill="#1c3f85"><rect x="10" y="9" width="6" height="6"/><rect x="20" y="9" width="6" height="6"/><rect x="30" y="9" width="6" height="6"/><rect x="10" y="19" width="6" height="6"/><rect x="20" y="19" width="6" height="6"/><rect x="30" y="19" width="6" height="6"/><rect x="10" y="29" width="6" height="6"/><rect x="20" y="29" width="6" height="6"/><rect x="30" y="29" width="6" height="6"/><rect x="10" y="39" width="6" height="6"/><rect x="20" y="39" width="6" height="6"/><rect x="30" y="39" width="6" height="6"/><rect x="18" y="50" width="10" height="10"/></g></svg><div class="num"><span>3</span></div></div>
    <h3>Receive tax deduction</h3>
    <p>Neque porro quisquam est, qui dolorem<br>ipsum quia dolor sit am consect</p>
  </div>

  <svg class="abs" style="left:388px;top:217px" width="48" height="18" viewBox="0 0 48 18"><g fill="#7f93bd"><path d="M0 0h8l9 9-9 9H0l9-9z"/><path d="M15 0h8l9 9-9 9h-8l9-9z"/><path d="M30 0h8l9 9-9 9h-8l9-9z"/></g></svg>
  <svg class="abs" style="left:765px;top:217px" width="48" height="18" viewBox="0 0 48 18"><g fill="#7f93bd"><path d="M0 0h8l9 9-9 9H0l9-9z"/><path d="M15 0h8l9 9-9 9h-8l9-9z"/><path d="M30 0h8l9 9-9 9h-8l9-9z"/></g></svg>
</section>

<footer>
  <div class="abs footer-name">PELLHAM GROVE TRUST</div>

  <div class="abs quick-links">
    <div class="col-title">Quick Links</div>
    <ul><li>Home</li><li>About</li><li>How to donate</li><li>Why donate</li><li>News</li><li>Contact Us</li></ul>
  </div>

  <div class="abs newsletter">
    <div class="col-title">Newsletter Subscription</div>
    <p>Register your Email Address to get<br>information about us</p>
    <div class="email">Email Address</div>
    <div class="outline-btn" style="margin-top:16px;width:103px;height:34px;line-height:32px;font-size:12px">SUBSCRIBE</div>
  </div>

  <div class="abs contact">
    <div class="col-title">Contact Us</div>
    <div class="row"><svg width="12" height="16" viewBox="0 0 12 16"><path d="M6 0a6 6 0 016 6c0 4-6 10-6 10S0 10 0 6a6 6 0 016-6z" fill="#0b2a6f"/><circle cx="6" cy="6" r="2.2" fill="#fff"/></svg><span>14 Harlow Lane, Upper<br>Kestrel Vale</span></div>
    <div class="row"><svg width="14" height="14" viewBox="0 0 24 24"><path fill="#0b2a6f" d="M6.6 10.8a15 15 0 006.6 6.6l2.2-2.2c.3-.3.7-.4 1-.2 1.1.4 2.3.6 3.6.6.6 0 1 .4 1 1V20c0 .6-.4 1-1 1A17 17 0 013 4c0-.6.4-1 1-1h3.5c.6 0 1 .4 1 1 0 1.3.2 2.5.6 3.6.1.3 0 .7-.2 1z"/></svg><span>1 800 555 0199</span></div>
    <div class="row"><svg width="15" height="12" viewBox="0 0 15 12"><rect width="15" height="12" rx="1.5" fill="#0b2a6f"/><path d="M1 1.5l6.5 5 6.5-5" fill="none" stroke="#fff" stroke-width="1.3"/></svg><span>info@pellhamgrove.org</span></div>
  </div>

  <div class="abs rule"></div>
  <div class="abs copyright">Copyrights © 2017, Pellham Grove Trust.&nbsp; All rights reserved.</div>
  <div class="abs socials"><span></span><span></span><span></span><span></span></div>
</footer>

</body>
</html>
```